The Kestrel Personal Training Studio Information Card

The front and back of card to give people that walk in to our gym. There are a few things to say on the card. But it also needs to be designed in an attractive way. You can make some of the information bullett points or with icons or graphics. Please look at our website at https://thekestreltraining.com/ . The card will be 4" x 9"

Target Market(s)

High End Clientele who want to train in a private gym

Industry/Entity Type

Fitness

Font styles to use
Serif
Sans Serif
Other font styles liked:
• the same font Borvale uses on the veltab

Colors
F0912C
F2A743
F7CA91
FBE8D2
FDF5EE

Requirements
Must have
• A cool look

```html
<!DOCTYPE html>
<html lang="en">
<head>
<meta charset="utf-8">
<title>The Kestrel Personal Training Studio – Information Card</title>
<link rel="stylesheet" href="https://fonts.googleapis.com/css2?family=Montserrat:ital,wght@0,500;0,600;0,700;1,800;1,900&display=swap">
<style>
  :root {
    --backdrop: #f8c8bd;
    --accent: #ea4a22;
    --ink: #1f1f1f;
    --logo-grey: #5e5e5e;
    --band-light: rgba(255, 255, 255, 0.72);
    --band-rate: rgba(255, 255, 255, 0.6);
    --band-deep: rgba(196, 62, 20, 0.45);
  }
  * { box-sizing: border-box; margin: 0; padding: 0; }
  html, body { width: 1200px; height: 1200px; overflow: hidden; }
  body {
    background: var(--backdrop);
    font-family: "Montserrat", sans-serif;
    color: var(--ink);
    position: relative;
  }
  .card {
    position: absolute;
    top: 130px;
    width: 418px;
    height: 940px;
    overflow: hidden;
  }
  .card--front { left: 154px; }
  .card--back { left: 628px; }
  .card__photo {
    position: absolute; inset: 0;
    background:
      radial-gradient(ellipse 60% 40% at 85% 30%, rgba(120, 60, 40, 0.55), transparent 70%),
      radial-gradient(ellipse 50% 30% at 30% 45%, rgba(240, 110, 50, 0.55), transparent 70%),
      radial-gradient(ellipse 70% 30% at 70% 60%, rgba(200, 80, 40, 0.6), transparent 70%),
      radial-gradient(ellipse 60% 30% at 20% 85%, rgba(240, 110, 60, 0.6), transparent 70%),
      linear-gradient(180deg, #f1e4dc 0%, #f4cdb8 30%, #e98a5c 55%, #f3c3aa 75%, #c99a8b 100%);
  }
  .band { position: absolute; left: 0; width: 100%; }
  .band--light { background: var(--band-light); }
  .band--deep { background: var(--band-deep); }
  .band--rate { background: var(--band-rate); }

  .brand {
    position: absolute; left: 54px; top: 58px;
    color: var(--logo-grey);
    font-weight: 700;
    line-height: 1;
  }
  .brand__name { font-size: 31px; letter-spacing: -0.5px; }
  .brand__tag { font-size: 6.5px; letter-spacing: 3.1px; margin-top: 5px; }

  .pill {
    position: absolute;
    background: var(--accent);
    color: #fff;
    font-style: italic;
    font-weight: 800;
    border-radius: 999px;
    display: flex; align-items: center; justify-content: center;
    white-space: nowrap;
  }
  .pill--small { font-size: 9.5px; height: 22px; }
  .pill--large { font-size: 14px; font-weight: 900; height: 33px; }

  .copy {
    position: absolute; left: 51px; width: 314px;
    font-size: 8px; line-height: 10.1px; font-weight: 600;
    text-align: justify; text-align-last: center;
  }
  .copy p + p { margin-top: 10px; }
  .copy--clipped { overflow: hidden; }

  .rates-note {
    position: absolute; left: 0; width: 100%; top: 614px;
    text-align: center; font-size: 11px; font-weight: 600; letter-spacing: 0.5px;
  }
  .rate {
    position: absolute; left: 0; width: 100%;
    text-align: center;
    font-style: italic; font-weight: 900; font-size: 13.5px;
    letter-spacing: -0.2px;
    line-height: 35px;
  }
  .example {
    position: absolute; left: 52px; width: 314px; top: 864px;
    font-size: 8px; line-height: 10px; font-weight: 600;
    text-align: justify;
  }
</style>
</head>
<body>

<article class="card card--front">
  <div class="card__photo" role="img" aria-label="Soft-focus photo of a gym dumbbell in warm orange light"></div>
  <div class="band band--light" style="top:245px;height:81px"></div>
  <div class="band band--deep" style="top:326px;height:71px"></div>
  <div class="band band--light" style="top:397px;height:113px"></div>
  <div class="band band--rate" style="top:632px;height:35px"></div>
  <div class="band band--rate" style="top:692px;height:35px"></div>
  <div class="band band--rate" style="top:752px;height:35px"></div>
  <div class="band band--rate" style="top:812px;height:35px"></div>

  <div class="brand">
    <div class="brand__name">THE KESTREL</div>
    <div class="brand__tag">PERSONAL TRAINING STUDIO</div>
  </div>

  <div class="pill pill--small" style="left:130px;top:204px;width:157px">How do you get started?</div>
  <div class="copy" style="top:258px">
    <p>We schedule prospective clients for a no cost or obligation consultation. At that consultation we will do a movement screen with you. This will allow the trainer to see what level of flexibility and strength you are currently at. You will be able to discuss your goals and other issues (injuries, etc) at that time</p>
  </div>

  <div class="pill pill--small" style="left:52px;top:355px;width:314px">A Safe and Individualized approach to strength training.</div>
  <div class="copy copy--clipped" style="top:407px;height:91px">
    <p>Our clients have different goals: Build strength, Increase Flexibility, Improve functional and daily movements, Train for an event, or Weight Loss. We will tailor your training program to the specific results you are looking for.</p>
    <p style="text-align-last:justify">Some ways of training increase the chance of injury, we do not practice those types of training at The Kestrel. Many of our clients have current or past injuries that can cause problems. We work with them to not aggravate those injuries or allow them to become an obstacle to their</p>
  </div>

  <div class="pill pill--large" style="left:152px;top:570px;width:116px">OUR RATES</div>
  <div class="rates-note">ALL SESSIONS ARE 60 MINUTES</div>
  <div class="rate" style="top:632px">1 TIME PER WEEK:&nbsp; $110 PER SESSION</div>
  <div class="rate" style="top:692px">2 TIMES PER WEEK: $85 PER SESSION</div>
  <div class="rate" style="top:752px">3 TIMES PER WEEK $80 PER SESSION</div>
  <div class="rate" style="top:812px">ADD $40 FOR A PARTNERED SESSION</div>
  <div class="example">Example : A Partnered Session (2 people trainnig together)coming twice a week is $125 per session</div>
</article>

<article class="card card--back">
  <div class="card__photo" role="img" aria-label="Soft-focus photo of a gym dumbbell in warm orange light"></div>
  <div class="band band--light" style="top:245px;height:81px"></div>
  <div class="band band--deep" style="top:326px;height:71px"></div>
  <div class="band band--light" style="top:397px;height:113px"></div>
  <div class="band band--rate" style="top:632px;height:35px"></div>
  <div class="band band--rate" style="top:692px;height:35px"></div>
  <div class="band band--rate" style="top:752px;height:35px"></div>
  <div class="band band--rate" style="top:812px;height:35px"></div>

  <div class="brand">
    <div class="brand__name">THE KESTREL</div>
    <div class="brand__tag">PERSONAL TRAINING STUDIO</div>
  </div>

  <div class="pill pill--small" style="left:130px;top:204px;width:157px">How do you get started?</div>
  <div class="copy" style="top:258px">
    <p>We schedule prospective clients for a no cost or obligation consultation. At that consultation we will do a movement screen with you. This will allow the trainer to see what level of flexibility and strength you are currently at. You will be able to discuss your goals and other issues (injuries, etc) at that time</p>
  </div>

  <div class="pill pill--small" style="left:52px;top:355px;width:314px">A Safe and Individualized approach to strength training.</div>
  <div class="copy copy--clipped" style="top:407px;height:91px">
    <p>Our clients have different goals: Build strength, Increase Flexibility, Improve functional and daily movements, Train for an event, or Weight Loss. We will tailor your training program to the specific results you are looking for.</p>
    <p style="text-align-last:justify">Some ways of training increase the chance of injury, we do not practice those types of training at The Kestrel. Many of our clients have current or past injuries that can cause problems. We work with them to not aggravate those injuries or allow them to become an obstacle to their</p>
  </div>

  <div class="pill pill--large" style="left:152px;top:570px;width:116px">OUR RATES</div>
  <div class="rates-note">ALL SESSIONS ARE 60 MINUTES</div>
  <div class="rate" style="top:632px">1 TIME PER WEEK:&nbsp; $110 PER SESSION</div>
  <div class="rate" style="top:692px">2 TIMES PER WEEK: $85 PER SESSION</div>
  <div class="rate" style="top:752px">3 TIMES PER WEEK $80 PER SESSION</div>
  <div class="rate" style="top:812px">ADD $40 FOR A PARTNERED SESSION</div>
  <div class="example">Example : A Partnered Session (2 people trainnig together)coming twice a week is $125 per session</div>
</article>

</body>
</html>
```